Two Versions of a Business Card for a Lawyer

Summary: I need a logo and a business card. The business card is two-sided and comes in two versions. One version is conservative, the other is slightly different with one or more pink embellishments in the logo or somewhere else in the business card.
I'm about to start off as a sole practitioner in criminal and immigration law. I'll largely be working with marginalised communities and in areas of social justice. One of my main focuses will be gendered violence, I'm hoping to specialise my practice towards representing victims of domestic and sexual violence and sex workers. I want a business card which would attract this clientele and make them feel safe to speak with me. I'd also like it to communicate a sense of hope.
However, the business card still has to be very conservative as the legal profession is very stuffy. So I was thinking of having two versions of the same card, one would be very straight forward while the other would have a **pink embellishment** or perhaps several. For example, if the scales of justice were used in the design, maybe the second version would have a pink flower about to bloom on the scale somewhere. Or maybe it's my logo that is different and pink.
While both designs have to be pretty conservative, I still want it to give off a sense that I'm alternative and think outside the box. With lawyers, I think a little bit of deviation goes a long way (less is more).
As far as colour goes (other than the pink embellishment), I was thinking something monochromatic, probably black and white but I am open to considering more colours. I personally love colour, and would love to use more colour, but am hesitant because of the nature of the profession. If you can find a way to use more colour while keeping it conservative and letting the pink pop, I'd be pretty pleased.
In general, I would prefer a clean simplistic design and logo. It should be immediately obvious that I'm a lawyer just by glancing at the card. I'm open to symbols of law, like the scales of justice or lady justice or something else. However, I don't want it to be the same as everyone else's.
Eventually, the design/style should be easy to recreate in the form of a website.
As far as the logo goes, it would probably use a circle as my last name starts with the letter "O". It can be very simple, with just my name and "Barrister & Solicitor". I don't currently have a logo, but the winning designer will be invited to provide a separate file for just the logo for an additional fee (I think it was CA$99). (Please ignore the uploaded logo file, it just wouldn't let me continue without uploading something).
As for the information that should go into the card, I'm still finalizing my address and phone number. So please use a placeholder for now.
Target Market(s)
Women, victims of sexual or domestic violence, refugees, people in need of legal services
Industry/Entity Type
Lawyer
Contact Information for Business Card
Marla Vent
Barrister & Solicitor
LL.B., B.C.L., B.F.A.
Criminal & Immigration Law
Street address
Toronto, ON
Postal Code
Phone number
Fax number
Email
Logo Text
Marla Vent, Barrister & Solicitor
Requirements
Must have
- Two versions
- One with pink
- Simplistic
Nice to have
- Maybe more colour
Should not have
- Not too conservative
- Not too predictable

```html
<!DOCTYPE html>
<html lang="en">
<head>
<meta charset="utf-8">
<title>Marla Vent — Business Card</title>
<link rel="stylesheet" href="https://fonts.googleapis.com/css2?family=Cinzel:wght@400;600;700&family=Lato:wght@400&display=swap">
<style>
  :root {
    --page-bg: #eceeef;
    --card-bg: #ffffff;
    --blossom-pink: #e05a7f;
    --blossom-deep: #e8708f;
    --blossom-soft: #f6b3c5;
    --blossom-pale: #fde6ed;
    --ink-navy: #1d2838;
    --ink-text: #222428;
  }
  * { margin: 0; padding: 0; box-sizing: border-box; }
  html, body {
    width: 1200px;
    height: 1000px;
    overflow: hidden;
    background: var(--page-bg);
  }
  .canvas {
    position: relative;
    width: 1200px;
    height: 1000px;
  }
  .card {
    position: absolute;
    top: 88px;
    width: 447px;
    height: 782px;
    background: var(--card-bg);
    box-shadow: 0 4px 14px rgba(0, 0, 0, 0.12);
    overflow: hidden;
    text-align: center;
  }
  .card--back { left: 128px; }
  .card--front { left: 623px; }

  .blossom-art {
    position: absolute;
    top: 0;
    left: 0;
    width: 100%;
    height: 450px;
    background: linear-gradient(180deg,
      var(--blossom-deep) 0%,
      var(--blossom-soft) 42%,
      var(--blossom-pale) 72%,
      var(--card-bg) 100%);
  }

  .practice-area {
    position: absolute;
    top: 456px;
    left: 0;
    width: 100%;
    font-family: 'Cinzel', serif;
    font-weight: 700;
    font-size: 20.5px;
    letter-spacing: 0.6px;
    white-space: nowrap;
    color: var(--blossom-pink);
  }
  .rule {
    position: absolute;
    left: 50%;
    width: 56px;
    height: 3px;
    margin-left: -28px;
    background: var(--ink-navy);
  }
  .rule--upper { top: 516px; }
  .rule--lower { top: 655px; }

  .contact {
    position: absolute;
    left: 0;
    width: 100%;
    font-family: 'Lato', sans-serif;
    font-size: 20.5px;
    line-height: 25.5px;
    letter-spacing: 1px;
    color: var(--ink-text);
  }
  .contact--lines { top: 553px; }
  .contact--address { top: 682px; }

  .holder-name {
    position: absolute;
    top: 562px;
    left: 0;
    width: 100%;
    font-family: 'Cinzel', serif;
    font-weight: 600;
    font-size: 44px;
    letter-spacing: 2.5px;
    white-space: nowrap;
    color: var(--blossom-pink);
  }
  .holder-title {
    position: absolute;
    top: 623px;
    left: 0;
    width: 100%;
    font-family: 'Cinzel', serif;
    font-weight: 400;
    font-size: 23px;
    line-height: 28px;
    letter-spacing: 1px;
    color: var(--ink-text);
  }
</style>
</head>
<body>
  <main class="canvas">
    <section class="card card--back" aria-label="Business card, contact side">
      <div class="blossom-art" role="img" aria-label="Watercolour cherry blossom branch with pink flowers and falling petals"></div>
      <p class="practice-area">CRIMINAL &amp; IMMIGRATION LAW</p>
      <span class="rule rule--upper"></span>
      <p class="contact contact--lines">
        000.555.2741<br>
        000.555.9316<br>
        marlavent@email.com
      </p>
      <span class="rule rule--lower"></span>
      <p class="contact contact--address">
        Your Street Address Here,<br>
        Toronto, 1234
      </p>
    </section>

    <section class="card card--front" aria-label="Business card, name side">
      <div class="blossom-art" role="img" aria-label="Watercolour cherry blossom branch with pink flowers and falling petals"></div>
      <h1 class="holder-name">MARLA VENT</h1>
      <p class="holder-title">
        Barrister &amp; Solicitor<br>
        LL.B., B.C.L., B.F.A.
      </p>
    </section>
  </main>
</body>
</html>
```